Surya Namaskar/Sun salutation theme based 12 months desk calendar for 2016 for an indian company

1. We are a corporate support services provider, providing services in Security Management, Fire Safety Management, facility management & HR Services based out of India. pls check website: www.brelvanta.co.in
2. Need a complete 12 months desk calendar design layout for 2016 including introductory page & end page,which can then be given for printing straightaway. The calendar should be so designed that when we open any month on the front side, the back side should also give out just the same month dates layout with space to note down any important work on a date etc..All important indian festivals, gazetted hoildays should be mentioned. Any information required can be provided by us
3. Since we give this calendars as part of new year gifts, our calendar has to compete for client desk space with other calendars, it must really be very sophisticated, sleek and attractive
4. Company logo, company contact details, website details and company works must be included in the calendar but in subtle, unobtrusive way. Few details like company logo etc, can be there on all pages.Am uploading some details, rest can be taken from the website, or can be provided
5. Calendar size should be aprx 17 cm * 17 cm including the space needed for spiral. Format should be CDR Ver13 or PDF
6. Theme: Surya Namaskar poses/Sun Salutation poses. These are twelve yoga poses, prescribed for mind /body rejuvenation. Poses 1-12 should be on months Jan16 to Dec 16. A very brief writeup on the same including the relevant mantras may also be included on the page
7. Any query , please mail to rohan.mehtra@brelvanta.co.in

Target Market(s)

corporate middle & senior management MNC clients

Industry/Entity Type

Security

Requirements
Must have
• 1.company logos/contact & website details/company works with related photographs.
• 2. surya namaskar poses with a very small brief/health benefit on poses/related mantras
• 3. Indian gazetted holidays & festivals earmarked
• 4. recommendation on the printing paper type & quality/colour of cardboard base & spiral binding
• 5. Attractive Top Introduction page & end page
Nice to have
• 1. photos of the company works
• 2. End page may be used for giving company details in details
• 3. Company logo on each page
• 4. The calendar goes to a variety of corporate clients including hotels, hospitals, shopping malls, manufacturing sector, clubs etc..just for info
• 5. Related photos/same model in all months
• 6. Beautiful Female models in poses
• 7. target audience : 95% male; majority age group: 35-55; middle & senior management
• However, very receptive to any new ideas. The designer has full liberty from our side. The final parameter is that the calendar should be so attractive that it can defeat any other desk calendar competition and win that one spot on the desk
• Any queries/details required, pls mail to rohan.mehtra@brelvanta.co.in
Should not have
• Religious overtones

```html
<!DOCTYPE html>
<html lang="en">
<head>
<meta charset="utf-8">
<title>Brelvanta Desk Calendar 2016 – February</title>
<link rel="stylesheet" href="https://fonts.googleapis.com/css2?family=Josefin+Sans:wght@400;600;700&family=Playfair+Display:ital,wght@1,800&family=Lora:ital,wght@1,500&display=swap">
<style>
  :root {
    --cream: #f7e8cb;
    --teal: #2a6b5f;
    --teal-text: #23665a;
    --sun-light: #f6cc28;
    --sun-deep: #f2981e;
    --wall-light: #f3f0ea;
    --wall-mid: #dcd6cc;
    --white: #ffffff;
  }
  html, body {
    margin: 0;
    padding: 0;
    width: 1200px;
    height: 1200px;
    overflow: hidden;
    background: var(--cream);
  }
  .page {
    position: relative;
    width: 1158px;
    height: 1158px;
    transform: scale(1.03627);
    transform-origin: 0 0;
    background: var(--cream);
    overflow: hidden;
  }
  .artwork {
    position: absolute;
    inset: 0;
    width: 1158px;
    height: 1158px;
  }
  .month-title {
    position: absolute;
    left: 540px;
    width: 586px;
    top: 62px;
    margin: 0;
    text-align: center;
    font-family: "Josefin Sans", sans-serif;
    font-weight: 600;
    font-size: 50px;
    letter-spacing: 1px;
    color: var(--teal-text);
  }
  .calendar {
    position: absolute;
    left: 540px;
    top: 120px;
    width: 586px;
    border-collapse: collapse;
    table-layout: fixed;
    font-family: "Josefin Sans", sans-serif;
    color: var(--teal-text);
  }
  .calendar th {
    font-weight: 700;
    font-size: 17px;
    height: 32px;
    padding: 0;
    vertical-align: top;
  }
  .calendar td {
    height: 82px;
    border: 1.5px solid var(--teal);
    text-align: right;
    vertical-align: top;
    padding: 2px 4px 0 0;
    font-weight: 700;
    font-size: 25px;
  }
  .mantra {
    position: absolute;
    left: 508px;
    top: 622px;
    margin: 0;
    font-family: "Playfair Display", serif;
    font-style: italic;
    font-weight: 800;
    font-size: 40px;
    line-height: 57px;
    color: var(--teal-text);
  }
  .meaning {
    position: absolute;
    left: 502px;
    top: 790px;
    margin: 0;
    font-family: "Lora", serif;
    font-style: italic;
    font-weight: 500;
    font-size: 33px;
    line-height: 47px;
    color: var(--teal-text);
  }
  .brand {
    position: absolute;
    left: 1012px;
    top: 1040px;
    width: 126px;
    text-align: center;
    font-family: "Josefin Sans", sans-serif;
    color: var(--white);
  }
  .brand-mark {
    display: block;
    width: 30px;
    height: 30px;
    margin: 0 auto 8px;
    background: var(--white);
    border-radius: 50%;
  }
  .brand-name {
    display: block;
    font-weight: 700;
    font-size: 17px;
    letter-spacing: 0.5px;
  }
  .brand-tagline,
  .brand-cert {
    display: block;
    font-size: 7px;
    font-weight: 400;
    line-height: 9px;
  }
</style>
</head>
<body>
<main class="page">
  <svg class="artwork" viewBox="0 0 1158 1158" xmlns="http://www.w3.org/2000/svg">
    <defs>
      <linearGradient id="wallTone" x1="0" y1="0" x2="0.6" y2="1">
        <stop offset="0" stop-color="var(--wall-light)"/>
        <stop offset="0.55" stop-color="var(--wall-mid)"/>
        <stop offset="1" stop-color="var(--wall-light)"/>
      </linearGradient>
      <linearGradient id="sunBand" x1="0" y1="0" x2="1" y2="0">
        <stop offset="0" stop-color="var(--sun-deep)"/>
        <stop offset="0.35" stop-color="var(--sun-light)"/>
        <stop offset="1" stop-color="var(--sun-deep)"/>
      </linearGradient>
    </defs>

    <rect class="pose-photo" role="img" aria-label="Photograph of a woman in a standing backward-bend yoga pose on a terrace in front of a white latticed window"
          x="0" y="0" width="480" height="720" fill="url(#wallTone)"/>

    <path class="sun-band"
          d="M0,728 L0,803 C180,792 360,774 480,757 L817,757 A76,76 0 0 0 817,605 L470,605 Z"
          fill="url(#sunBand)"/>

    <path class="frame-curve"
          d="M395,0 C402,200 410,420 410,570 C410,660 385,690 320,690 C220,690 100,640 0,615
             L0,770 C150,760 300,750 390,745 C460,740 490,690 490,590 C490,420 470,200 456,0 Z"
          fill="var(--teal)"/>

    <path class="corner-curve"
          d="M962,1158 C968,1040 1040,962 1158,960 L1158,1158 Z"
          fill="var(--teal)"/>
  </svg>

  <h1 class="month-title">FEBRUARY</h1>
  <table class="calendar">
    <thead>
      <tr><th>SUN</th><th>MON</th><th>TUE</th><th>WED</th><th>THU</th><th>FRI</th><th>SAT</th></tr>
    </thead>
    <tbody>
      <tr><td></td><td>1</td><td>2</td><td>3</td><td>4</td><td>5</td><td>6</td></tr>
      <tr><td>7</td><td>8</td><td>9</td><td>10</td><td>11</td><td>12</td><td>13</td></tr>
      <tr><td>14</td><td>15</td><td>16</td><td>17</td><td>18</td><td>19</td><td>20</td></tr>
      <tr><td>21</td><td>22</td><td>23</td><td>24</td><td>25</td><td>26</td><td>27</td></tr>
      <tr><td>28</td><td>29</td><td>30</td><td>31</td><td></td><td></td><td></td></tr>
    </tbody>
  </table>

  <p class="mantra">2. Om Hreem<br>Ravaye Namah</p>
  <p class="meaning">Prostration to Him<br>who is the cause for change.</p>

  <div class="brand">
    <span class="brand-mark"></span>
    <span class="brand-name">BRELVANTA</span>
    <span class="brand-tagline">Your one stop business companion</span>
    <span class="brand-cert">ISO 9001:2008 Certified</span>
  </div>
</main>
</body>
</html>
```